Torvane Halbridge

Looking for modern business cards.
Clean contemporary design.
Similar to this.
https://www.plumvexa-search.example/imgres?imgurl=https%3A%2F%2Fimg.quorlint-cdn.example%2Fsleek_dark_metal_card_design_540.jpg&imgrefurl=https%3A%2F%2Fwww.quorlint-prints.example%2Fsleek_dark_metal_card_design-918273645501928374&q=modern%20business%20cards

But I'd like the blue to look metallic.

Business

```html
<!DOCTYPE html>
<html lang="en">
<head>
<meta charset="utf-8">
<title>Torvane Halbridge – Business Card</title>
<link rel="stylesheet" href="https://fonts.googleapis.com/css2?family=Arimo:wght@400;700&family=PT+Sans:wght@400;700&display=swap">
<style>
  :root {
    --backdrop: #242424;
    --card-white: #ffffff;
    --navy: #1d4a6a;
    --sky: #1b9cc6;
    --ink: #1a1a1a;
    --rule: #7a8094;
    --accent: #e8391d;
    --steel-dark: #1d6d8e;
    --steel-mid: #1aa3c9;
    --steel-light: #5cc3dd;
  }
  * { margin: 0; padding: 0; box-sizing: border-box; }
  html, body { width: 1200px; height: 900px; overflow: hidden; }
  body { background: var(--backdrop); position: relative; font-family: "PT Sans", sans-serif; }

  .card {
    position: absolute;
    top: 170px;
    width: 347px;
    height: 561px;
    box-shadow: 3px 4px 6px rgba(0,0,0,0.45);
  }
  .card--front { left: 259px; background: var(--card-white); }
  .card--back {
    left: 631px;
    background:
      radial-gradient(ellipse at 35% 55%, rgba(255,255,255,0.18) 0%, rgba(255,255,255,0) 55%),
      linear-gradient(135deg, var(--steel-dark) 0%, var(--steel-mid) 35%, var(--steel-light) 52%, var(--steel-mid) 68%, var(--steel-dark) 100%);
  }

  .brand {
    position: absolute;
    display: flex;
    align-items: center;
    gap: 8px;
    font-family: "Arimo", sans-serif;
    font-weight: 400;
    white-space: nowrap;
  }
  .brand__dot { width: 11px; height: 11px; border-radius: 50%; flex: none; }
  .card--front .brand { left: 30px; top: 176px; font-size: 27px; color: var(--navy); }
  .card--front .brand__dot { background: var(--accent); }
  .card--back .brand { left: 28px; top: 432px; font-size: 27px; color: #ffffff; }
  .card--back .brand__dot { background: #ffffff; }

  .contact {
    position: absolute;
    left: 0; right: 0;
    top: 343px;
    text-align: center;
    color: var(--ink);
  }
  .contact__name {
    font-family: "Arimo", sans-serif;
    font-weight: 700;
    font-size: 20px;
    letter-spacing: 0.3px;
    color: var(--navy);
    line-height: 24px;
  }
  .contact__name span { color: var(--sky); }
  .contact__title { font-size: 15px; line-height: 18px; }
  .contact__rule {
    width: 157px; height: 1px; margin: 13px auto 10px;
    background: var(--rule);
  }
  .contact__line { font-size: 15px; line-height: 21px; }
  .contact__line b { color: var(--navy); }
  .contact__web { font-weight: 700; color: var(--navy); }
  .contact__web span { color: var(--sky); }
  .contact__address { font-size: 15px; line-height: 17px; }
</style>
</head>
<body>
  <section class="card card--front" aria-label="Card front">
    <div class="brand">
      <span class="brand__name">Torvane Halbridge</span>
      <span class="brand__dot"></span>
    </div>

    <div class="contact">
      <h1 class="contact__name">OREN <span>CASTELL</span></h1>
      <p class="contact__title">Managing Director</p>
      <div class="contact__rule"></div>
      <p class="contact__line"><b>P:</b> 823-555-0147</p>
      <p class="contact__line"><b>E:</b> info@halbridge.example</p>
      <p class="contact__line contact__web">www.<span>halbridge</span>.example</p>
      <div class="contact__rule"></div>
      <p class="contact__address">1234, Address Goes Here</p>
      <p class="contact__address">Country Name, 123456</p>
    </div>
  </section>

  <section class="card card--back" aria-label="Card back, metallic blue">
    <div class="brand">
      <span class="brand__name">Torvane Halbridge</span>
      <span class="brand__dot"></span>
    </div>
  </section>
</body>
</html>
```